Event Website Design

We need a new website design for an events driven website. The domain for this site is http://brackmoorhalls.co.uk. The site is up and running but needs a new fresh, modern look.
I've attached a Balamiq Mockup for the layout of the home page. Also attached is a png of the logo.
Key colours for the site are 0f7e6a, 35bde, d57835 & 373737.
Font to use is Proxima Nova
Width of the site should be 1200px
The design should be contemporary with minimal clutter.
Websites to references are…
http://vorpin.london/
http://www.darvushall.co.uk/
These are just guidelines, please feel free to use you own creative judgment.
The selected design file needs to be supplied as an editable PSD.
Reason: I've submitted 5 designs to the client, who will select the one they want. I will then choose that design. So please be patient as I'm waiting for a decision from my client.
Industry/Entity Type
Events
Number of Pages Required
1 page
Look and feel
Each slider illustrates characteristics of the customer's brand and the style your logo design should communicate.

```html
<!DOCTYPE html>
<html lang="en">
<head>
<meta charset="utf-8">
<title>Brackmoor Halls – Home</title>
<link rel="stylesheet" href="https://fonts.googleapis.com/css2?family=Figtree:wght@300;400;500;600;700&display=swap">
<style>
:root{
  --teal:#0f7e6a;
  --blue:#135bde;
  --orange:#d57835;
  --charcoal:#373737;
  --nav:#1f1f1f;
  --ink:#4a4a4a;
  --muted:#8a8a8a;
  --line:#e2e2e2;
  --white:#ffffff;
}
*{margin:0;padding:0;box-sizing:border-box}
html,body{width:1200px;height:2436px;overflow:hidden}
body{font-family:"Figtree",Arial,sans-serif;background:var(--white);color:var(--ink);position:relative}

/* Header */
.site-header{position:absolute;left:0;top:0;width:1200px;height:143px;background:var(--charcoal)}
.utility-links{position:absolute;right:72px;top:11px;display:flex;font-size:12px;color:#cfcfcf}
.utility-links span{padding:0 9px;border-left:1px solid #555}
.utility-links span:first-child{border-left:0}
.brand{position:absolute;left:146px;top:62px;display:flex;align-items:center;gap:9px}
.brand-mark{width:18px;height:18px;background:var(--teal)}
.brand-name{font-size:22px;font-weight:700;color:var(--white);letter-spacing:.5px}
.brand-tagline{position:absolute;left:146px;top:110px;font-size:14px;color:#d8d8d8}
.box-office{position:absolute;left:495px;top:66px;font-size:21px;font-weight:500;color:var(--white)}
.search{position:absolute;left:781px;top:64px;width:172px;height:29px;border:1px solid #8a8a8a;border-radius:15px;display:flex;align-items:center;padding-left:12px;gap:7px;font-size:12px;color:#bbb}
.social-top{position:absolute;left:968px;top:63px;display:flex;gap:5px}
.social-top i{width:27px;height:27px;border:2px solid var(--white);border-radius:50%;display:block}

.main-nav{position:absolute;left:0;top:143px;width:1200px;height:47px;background:var(--nav);display:flex;align-items:center;padding-left:143px;font-size:15px;font-weight:600;color:var(--white)}
.main-nav a{padding:0 11px;border-left:1px solid #4a4a4a;line-height:20px}
.main-nav a:first-child{padding-left:0;border-left:0}

/* Hero */
.hero{position:absolute;left:0;top:190px;width:1200px;height:473px;background:radial-gradient(ellipse at 30% 40%,#b3202a 0%,#6e1016 45%,#200406 100%)}
.hero-panel{position:absolute;left:143px;top:374px;width:406px;height:198px;background:rgba(19,91,222,.92);padding:22px 33px;color:var(--white)}
.hero-panel h1{font-size:30px;font-weight:500;line-height:1.1}
.hero-panel .date{font-size:16px;margin-top:6px;color:#dbe6fb}
.hero-panel p{font-size:12.5px;line-height:18px;margin-top:12px;color:#e6edfc}
.btn-row{display:flex;gap:12px;margin-top:16px}
.btn-outline{border:2px solid var(--white);font-size:11px;font-weight:600;padding:5px 0;width:82px;text-align:center;letter-spacing:.5px}
.slider-dots{position:absolute;left:557px;top:631px;display:flex;gap:8px}
.slider-dots i{width:14px;height:14px;border-radius:50%;background:var(--white);display:block}
.slider-dots i:first-child{background:transparent;border:2px solid var(--white)}

/* Event cards */
.events-row{position:absolute;left:143px;top:690px;display:flex;gap:10px}
.event-card{width:221px;height:236px;border:1px solid var(--line);background:var(--white)}
.event-thumb{height:133px}
.thumb-1{background:linear-gradient(180deg,#1a2a8c,#3b6fe0 60%,#0c1033)}
.thumb-2{background:linear-gradient(180deg,#3a5d9a,#8a6a52 60%,#3a2a22)}
.thumb-3{background:linear-gradient(180deg,#8a6a38,#e2d5c0 60%,#c7b8a2)}
.thumb-4{background:linear-gradient(180deg,#2a1a5a,#8b4aa8 55%,#1a0f2a)}
.event-body{padding:10px 19px 0}
.event-body h3{font-size:15.5px;font-weight:500;color:var(--teal)}
.event-body .date{font-size:12.5px;color:var(--muted);margin-top:6px}
.card-btns{display:flex;gap:8px;margin-top:9px}
.card-btns span{width:88px;height:27px;line-height:27px;text-align:center;font-size:11px;font-weight:600;color:var(--white)}
.btn-more{background:var(--orange)}
.btn-book{background:var(--teal)}
.arrow{position:absolute;top:785px}

/* News */
.news{position:absolute;left:0;top:976px;width:1200px;height:372px;background:linear-gradient(160deg,var(--teal) 10%,#5b7d4f 50%,var(--orange) 95%);color:var(--white)}
.news h2{position:absolute;left:145px;top:52px;font-size:33px;font-weight:400}
.news .see-all{position:absolute;left:145px;top:97px;font-size:15px;letter-spacing:.5px;color:#cfe5df}
.news-item{position:absolute;top:152px;width:270px}
.news-item h3{font-size:18.5px;font-weight:400}
.news-item p{font-size:12.5px;line-height:19.5px;margin-top:12px;color:#d4e4de}
.read-more{display:flex;align-items:center;gap:6px;font-size:12.5px;margin-top:12px}

/* Feature tiles */
.tiles{position:absolute;left:143px;top:1403px;display:flex;gap:11px}
.tile{width:298px;height:275px;color:var(--white);text-align:center;padding-top:40px}
.tile-conf{background:linear-gradient(160deg,#1d8a6e,#0f6a55)}
.tile-party{background:linear-gradient(160deg,#e08a4c,#c86a2c)}
.tile-cowork{background:linear-gradient(160deg,#2a6ef0,#0f52d0)}
.tile h3{font-size:22px;font-weight:400;margin-top:14px}
.tile p{font-size:12.5px;line-height:18px;margin:6px auto 0;width:230px;color:#eef}
.tile .btn-outline{margin:16px auto 0;width:88px}

/* Sports */
.sports{position:absolute;left:0;top:1730px;width:1200px;height:380px;background:linear-gradient(180deg,#e9ecef 0%,#d8dee2 55%,#b98d5e 80%,#a87a4c 100%)}
.sports-box{position:absolute;left:403px;top:130px;width:390px;height:110px;border:2px solid var(--white);padding:8px}
.sports-box-inner{background:rgba(255,255,255,.85);height:100%;text-align:center;padding-top:14px}
.sports-box h2{font-size:37px;font-weight:400;color:var(--blue)}
.sports-box p{font-size:16px;color:var(--orange);margin-top:2px}

/* Footer */
.footer-col{position:absolute;top:2174px;font-size:14px;line-height:25.5px;color:var(--ink);font-style:normal}
.footer-brand{position:absolute;left:848px;top:2198px;display:flex;align-items:center;gap:8px}
.footer-brand .brand-mark{width:16px;height:16px}
.footer-brand .brand-name{font-size:20px;color:var(--charcoal)}
.footer-social{position:absolute;left:667px;top:2289px;display:flex;gap:6px}
.footer-social i{width:25px;height:25px;border-radius:50%;display:block}
.footer-rule{position:absolute;left:0;top:2371px;width:1200px;height:1px;background:var(--line)}
.copyright{position:absolute;left:0;width:1200px;top:2395px;text-align:center;font-size:11.5px;color:#b5b5b5}
</style>
</head>
<body>

<header class="site-header">
  <nav class="utility-links"><span>Gift Voucher</span><span>Join Our Mailing List</span><span>My Account</span><span>Basket</span><span>Register</span></nav>
  <div class="brand"><span class="brand-mark"></span><span class="brand-name">BRACKMOOR HALLS</span></div>
  <div class="brand-tagline">Dunshire's Favourite Entertainment &amp; Leisure Venue</div>
  <div class="box-office">Box Office: 01632 960 482</div>
  <div class="search">
    <svg width="12" height="12" viewBox="0 0 12 12"><circle cx="5" cy="5" r="3.8" fill="none" stroke="#ddd" stroke-width="1.5"/><line x1="8" y1="8" x2="11" y2="11" stroke="#ddd" stroke-width="1.5"/></svg>
    Search
  </div>
  <div class="social-top"><i></i><i></i><i></i></div>
</header>

<nav class="main-nav">
  <a>What's On</a><a>Conferencing &amp; Events</a><a>Sports &amp; Leisure</a><a>Lantern Theatre</a><a>Plan Your Visit</a><a>News</a><a>Discover More</a><a>Contact Us</a>
</nav>

<section class="hero" role="img" aria-label="Photo of a concert crowd with raised hands under red stage lights"></section>
<div class="hero-panel">
  <h1>Show/Party Tittle here</h1>
  <div class="date">Mon 07 Jan</div>
  <p>Class aptent taciti sociosqu ad litora torquent per conubia nostra per inceptos hymenaeos Proin nulla arcu</p>
  <div class="btn-row"><span class="btn-outline">MORE</span><span class="btn-outline">BOOK</span></div>
</div>
<div class="slider-dots"><i></i><i></i><i></i><i></i></div>

<svg class="arrow" style="left:114px" width="14" height="24" viewBox="0 0 14 24"><polyline points="12,2 2,12 12,22" fill="none" stroke="#c8c8c8" stroke-width="2"/></svg>
<svg class="arrow" style="left:1064px" width="14" height="24" viewBox="0 0 14 24"><polyline points="2,2 12,12 2,22" fill="none" stroke="#c8c8c8" stroke-width="2"/></svg>

<section class="events-row">
  <article class="event-card"><div class="event-thumb thumb-1" role="img" aria-label="Photo of an arena lit in blue"></div><div class="event-body"><h3>Show Tittle here</h3><div class="date">Mon 7 Jan</div><div class="card-btns"><span class="btn-more">MORE</span><span class="btn-book">BOOK</span></div></div></article>
  <article class="event-card"><div class="event-thumb thumb-2" role="img" aria-label="Photo of a conference audience facing a screen"></div><div class="event-body"><h3>Show Tittle here</h3><div class="date">Mon 7 Jan</div><div class="card-btns"><span class="btn-more">MORE</span><span class="btn-book">BOOK</span></div></div></article>
  <article class="event-card"><div class="event-thumb thumb-3" role="img" aria-label="Photo of a banquet hall with chandeliers"></div><div class="event-body"><h3>Show Tittle here</h3><div class="date">Wed 9 Jan</div><div class="card-btns"><span class="btn-more">MORE</span><span class="btn-book">BOOK</span></div></div></article>
  <article class="event-card"><div class="event-thumb thumb-4" role="img" aria-label="Photo of fireworks over a party crowd"></div><div class="event-body"><h3>Show Tittle here</h3><div class="date">Sun 15 Jan</div><div class="card-btns"><span class="btn-more">MORE</span><span class="btn-book">BOOK</span></div></div></article>
</section>

<section class="news">
  <h2>Latest from Brackmoor Halls</h2>
  <div class="see-all">SEE ALL NEWS</div>
  <article class="news-item" style="left:143px"><h3>Curabitur iaculis tempus</h3><p>Class aptent taciti sociosqu ad litora torquent per conubia nostra per inceptos hymenaeos Proin nulla arcu nonummy luctus dictum eget fermentum et lorem um eget fe</p><div class="read-more">READ MORE <svg width="18" height="18" viewBox="0 0 18 18"><circle cx="9" cy="9" r="7.5" fill="none" stroke="#fff" stroke-width="1.3"/><polyline points="7.5,5.5 11,9 7.5,12.5" fill="none" stroke="#fff" stroke-width="1.3"/></svg></div></article>
  <article class="news-item" style="left:472px"><h3>Donec convallis pede venenatis</h3><p>Class aptent taciti sociosqu ad litora torquent per conubia nostra per inceptos hymenaeos Proin nulla arcu nonummy luctus dictum eget fermentum et lorem um eget fe</p><div class="read-more">READ MORE <svg width="18" height="18" viewBox="0 0 18 18"><circle cx="9" cy="9" r="7.5" fill="none" stroke="#fff" stroke-width="1.3"/><polyline points="7.5,5.5 11,9 7.5,12.5" fill="none" stroke="#fff" stroke-width="1.3"/></svg></div></article>
  <article class="news-item" style="left:802px"><h3>Aliquam erat volutpat</h3><p>Class aptent taciti sociosqu ad litora torquent per conubia nostra per inceptos hymenaeos Proin nulla arcu nonummy luctus dictum eget fermentum et lorem um eget fe</p><div class="read-more">READ MORE <svg width="18" height="18" viewBox="0 0 18 18"><circle cx="9" cy="9" r="7.5" fill="none" stroke="#fff" stroke-width="1.3"/><polyline points="7.5,5.5 11,9 7.5,12.5" fill="none" stroke="#fff" stroke-width="1.3"/></svg></div></article>
</section>

<section class="tiles">
  <article class="tile tile-conf" role="img" aria-label="Green-tinted photo of a conference presenter">
    <svg width="76" height="62" viewBox="0 0 76 62" fill="none" stroke="#fff" stroke-width="2"><circle cx="38" cy="16" r="9"/><circle cx="16" cy="22" r="7"/><circle cx="60" cy="22" r="7"/><path d="M22 56v-8a16 16 0 0 1 32 0v8z"/><path d="M4 56v-6a12 12 0 0 1 18-10"/><path d="M72 56v-6a12 12 0 0 0-18-10"/></svg>
    <h3>Conference &amp; Events</h3>
    <p>Proin nulla arcu nonummy luctus dictum eget fermentum et lorem um</p>
    <div class="btn-outline">MORE</div>
  </article>
  <article class="tile tile-party" role="img" aria-label="Orange-tinted photo of guests at a party">
    <svg width="76" height="62" viewBox="0 0 76 62" fill="none" stroke="#fff" stroke-width="2"><path d="M24 14h16l-4 20a6 6 0 0 1-8 0z"/><line x1="32" y1="36" x2="32" y2="56"/><line x1="24" y1="56" x2="40" y2="56"/><path d="M44 12l14 4-8 18a6 6 0 0 1-8-2z"/><line x1="46" y1="34" x2="42" y2="54"/><line x1="36" y1="52" x2="48" y2="56"/><circle cx="56" cy="6" r="2"/><circle cx="62" cy="10" r="1.5"/></svg>
    <h3>Parties at Brackmoor</h3>
    <p>Proin nulla arcu nonummy luctus dictum eget fermentum et lorem um</p>
    <div class="btn-outline">MORE</div>
  </article>
  <article class="tile tile-cowork" role="img" aria-label="Blue-tinted photo of people working together">
    <svg width="76" height="62" viewBox="0 0 76 62" fill="none" stroke="#fff" stroke-width="2.4"><path d="M22 12h26a8 8 0 0 1 8 8v8a8 8 0 0 1-8 8H34l-8 7v-7h-4a8 8 0 0 1-8-8v-8a8 8 0 0 1 8-8z"/><path d="M58 26a8 8 0 0 1 6 8v6a8 8 0 0 1-8 8h-2v6l-8-6h-8"/></svg>
    <h3>Co-Working Hub</h3>
    <p>Proin nulla arcu nonummy luctus dictum eget fermentum et lorem um</p>
    <div class="btn-outline">MORE</div>
  </article>
</section>

<section class="sports" role="img" aria-label="Photo of a fitness class doing press-ups on blue mats">
  <div class="sports-box"><div class="sports-box-inner"><h2>Sports &amp; Leisure</h2><p>Click here for more Information</p></div></div>
</section>

<footer>
  <address class="footer-col" style="left:146px">Brackmoor Entertainment Venue<br>Fernley Close<br>Marlcombe Dunshire<br>MC4 7QX</address>
  <div class="footer-col" style="left:425px">What's On<br>Conferencing &amp; Events<br>Sports &amp; Leisure<br>Lantern Theatre</div>
  <div class="footer-col" style="left:667px">Plan Your Visit<br>News<br>Discover More<br>Contact Us</div>
  <div class="footer-social"><i style="background:#3fa7e0"></i><i style="background:#2f5b9a"></i><i style="background:#1f73b0"></i><i style="background:#d0452f"></i></div>
  <div class="footer-brand"><span class="brand-mark"></span><span class="brand-name">BRACKMOOR HALLS</span></div>
  <div class="footer-rule"></div>
  <div class="copyright">© 2016 Company Name &nbsp;All right reserved &nbsp;Term of Use</div>
</footer>

</body>
</html>
```